Basic / Quick Business Card

Quick easy design project!

Need a one sided basic business card that matches font & style of brand and bottle label for our gourmet condiment, Brindle Harrow Sauce. Brindle Harrow Sauce is sold in specialty retail, gourmet groceries and appears on chef-driven restaurant menus, so the target market is a high end, gourmet, artisan-made food-loving customer.

Files Included:
Sauce Bottle Label
Brindle Harrow Sauce Round Logos

**About the logos - the logo may be used in a circle or alone vertically as on side of the bottle label**

Layout of Card:
May be vertical or horizontal based on designer ideas.

Logo usage (in circle vs. stand alone vertical logo) is up to designers descretion as well.

Reverse side of business card will be various high end / professional product photos / food shots using us.kelbo.com system. **Designer on this project will NOT design a reserve for the card.**

Paper that will be used for printing:
Kelbo Standard - it's a WHITE paper, but we use a cream background on Brindle Harrow Sauce branding, so please take this into account on design to stay brand consistent.

Elements & Copy for Card:
1. Logo in either script horizontal or vertical version
2. Copy: "Artisan Made - Small Batch"
3. Name - Wes Dorrance
4. Title - Creator
5. Phone - xxx.xxx.xxxx
6. xxxx@brindleharrow.com
7. URL: brindleharrowsauce.com
8. Social Media: @getbrindleharrow on Quillo / Pagora / Lumigrid

Please provide final files in Illustrator or InDesign format.

```html
<!DOCTYPE html>
<html lang="en">
<head>
<meta charset="utf-8">
<title>Brindle Harrow Sauce – Business Card</title>
<link href="https://fonts.googleapis.com/css2?family=Marcellus&display=swap" rel="stylesheet">
<style>
  :root {
    --backdrop: #d9d4cc;
    --card-dark: #2a2927;
    --panel-cream: #eef0dc;
    --brand-yellow: #f2ae1c;
    --ink: #2b2a26;
    --white: #ffffff;
  }
  * { margin: 0; padding: 0; box-sizing: border-box; }
  html, body {
    width: 1200px; height: 833px; overflow: hidden;
    background: var(--backdrop);
    font-family: "Marcellus", serif;
  }
  .canvas {
    position: relative; width: 1200px; height: 833px;
  }
  .card {
    position: absolute; left: 100px; top: 131px;
    width: 1000px; height: 571px;
    background: var(--card-dark);
    box-shadow: 0 10px 30px rgba(0,0,0,.25);
  }
  .brand-mark {
    position: absolute; left: 85px; top: 140px;
    width: 290px; height: 290px;
    border: 6px solid var(--brand-yellow);
    border-radius: 50%;
    display: flex; align-items: center; justify-content: center;
    text-align: center;
  }
  .brand-name {
    color: var(--brand-yellow);
    font-size: 40px; line-height: 1.1;
  }
  .info-panel {
    position: absolute; left: 500px; top: 25px;
    width: 475px; height: 521px;
    background: var(--panel-cream);
  }
  .name-bar {
    position: absolute; left: 0; top: 35px;
    width: 440px; height: 70px;
    background: var(--brand-yellow);
    color: var(--white);
    font-size: 34px; line-height: 70px;
    padding-left: 20px;
  }
  .contact-list {
    position: absolute; left: 24px; top: 180px;
    list-style: none;
    color: var(--ink); font-size: 23px;
  }
  .contact-list li {
    display: flex; align-items: center; gap: 10px;
    height: 36px;
  }
  .contact-list svg { width: 20px; height: 20px; flex: none; }
  .dotted-rule {
    position: absolute; left: 24px; width: 425px;
    border-top: 4px dotted var(--brand-yellow);
  }
  .rule-one { top: 300px; }
  .rule-two { top: 400px; }
  .follow {
    position: absolute; left: 24px; top: 330px;
    display: flex; align-items: center; gap: 12px;
    color: var(--ink); font-size: 22px;
  }
  .social-name { font-size: 17px; }
  .tagline {
    position: absolute; left: 24px; top: 440px;
    color: var(--ink); font-size: 27px;
  }
</style>
</head>
<body>
<main class="canvas">
  <section class="card">
    <div class="brand-mark">
      <span class="brand-name">Brindle<br>Harrow<br>Sauce</span>
    </div>

    <div class="info-panel">
      <h1 class="name-bar">Wes Dorrance, Creator</h1>

      <ul class="contact-list">
        <li>
          <svg viewBox="0 0 20 20" aria-hidden="true"><circle cx="10" cy="10" r="8.5" fill="none" stroke="#2b2a26" stroke-width="1.6"/><path d="M7 5.5c-1 1-1 3 1 5.5s4 3.5 5 2.5l-1.5-1.8-1.2.6c-1-.6-2-1.8-2.5-2.9l.8-1z" fill="#2b2a26"/></svg>
          123-456-7890
        </li>
        <li>
          <svg viewBox="0 0 20 20" aria-hidden="true"><path d="M2 7l8-4 8 4v9H2z" fill="#2b2a26"/><path d="M3 8l7 5 7-5" fill="none" stroke="#eef0dc" stroke-width="1.4"/></svg>
          wdorrance@brindleharrow.com
        </li>
        <li>
          <svg viewBox="0 0 20 20" aria-hidden="true"><g fill="none" stroke="#2b2a26" stroke-width="1.5"><circle cx="10" cy="10" r="8"/><ellipse cx="10" cy="10" rx="3.5" ry="8"/><path d="M2 10h16M3.5 6h13M3.5 14h13"/></g></svg>
          www.brindleharrowsauce.com
        </li>
      </ul>

      <div class="dotted-rule rule-one"></div>

      <p class="follow">Follow Us On
        <span class="social-name">Pagora</span>
        <span class="social-name">Quillo</span>
        <span class="social-name">Lumigrid</span>
      </p>

      <div class="dotted-rule rule-two"></div>

      <p class="tagline">Artisan Made - Small Batch</p>
    </div>
  </section>
</main>
</body>
</html>
```